Corporate Design für logopädische Praxis
Zielgruppe
Ich gründe eine logopädische Praxis, die Sprachtherapie sowohl für Erwachsene als auch Kinder anbietet und damit ein Logo benötigt, das jede Altersgruppe anspricht und 'Lindenhof' als fachliche und menschliche Qualitätszeit interpretiert.
Aufgabenstellung
Ich bevorzuge ein klares Design, welches das Wortspiel der 'Lindenhof' im Idealfall aufgreift und den Patienten vermittelt, dass sowohl die fachliche Qualität der Behandlung als auch die Ebene von Empathie und Patientenorientierung im zwischenmenschlichen Umgang für die Praxis zentral sind.

```html
<!DOCTYPE html>
<html lang="de">
<head>
<meta charset="utf-8">
<title>Lindenhof – Praxis für Logopädie</title>
<link href="https://fonts.googleapis.com/css2?family=Poppins:wght@300;400&display=swap" rel="stylesheet">
<style>
  :root {
    --mauve: #978092;
    --rose: #c9aba3;
    --ink: #5b4c4c;
    --page: #ffffff;
    --panel: #f6f6f6;
    --rule: #dddddd;
  }
  * { margin: 0; padding: 0; box-sizing: border-box; }
  html, body { width: 937px; height: 1200px; overflow: hidden; }
  body {
    position: relative;
    background: var(--page);
    font-family: "Poppins", sans-serif;
    font-weight: 300;
    color: var(--ink);
  }
  .brand-panel {
    position: absolute; left: 20px; top: 20px; width: 897px; height: 390px;
    border: 1px solid var(--rule);
    background: radial-gradient(ellipse at center, #ffffff 45%, var(--panel) 100%);
    display: flex; flex-direction: column; align-items: center; justify-content: center;
  }
  .wordmark {
    display: flex; align-items: center; gap: 10px;
    color: var(--mauve); font-weight: 300; line-height: 1;
  }
  .wordmark .dot { border-radius: 50%; background: var(--rose); flex: none; }
  .brand-panel .wordmark { font-size: 64px; gap: 16px; }
  .brand-panel .wordmark .dot { width: 26px; height: 26px; }
  .tagline { letter-spacing: 0.12em; color: var(--ink); }
  .brand-panel .tagline { font-size: 22px; margin-top: 26px; }

  .card {
    position: absolute; left: 42px; width: 318px; height: 200px;
    background: #fff; overflow: hidden;
    box-shadow: 0 1px 3px rgba(0,0,0,0.15);
  }
  .card-hours { top: 560px; }
  .card-contact { top: 820px; }
  .card .head {
    height: 124px; display: flex; flex-direction: column; align-items: center; justify-content: center;
  }
  .card .wordmark { font-size: 30px; }
  .card .wordmark .dot { width: 12px; height: 12px; }
  .card .tagline { font-size: 10px; margin-top: 8px; color: #9f9296; }
  .card .band {
    position: absolute; left: 0; right: 0; bottom: 0;
    background: var(--mauve); color: #fff;
    border-top: 3px solid #fff; box-shadow: 0 -2px 0 var(--rose);
    text-align: center; font-size: 9.5px; line-height: 1.35;
    display: flex; flex-direction: column; justify-content: center;
  }
  .card-hours .band { height: 70px; }
  .card-contact .head { height: 92px; }
  .card-contact .band { height: 104px; }
  .card-contact .band .name { font-size: 17px; font-weight: 300; }
  .card-contact .band .sub { font-size: 9px; margin-bottom: 8px; }

  .letterhead {
    position: absolute; left: 428px; top: 456px; width: 472px; height: 668px;
    background: #fff; box-shadow: 3px 4px 8px rgba(0,0,0,0.3);
  }
  .letterhead .top-band { height: 9px; background: var(--rose); }
  .letterhead .sender-logo {
    position: absolute; right: 22px; top: 60px;
    display: flex; flex-direction: column; align-items: center;
  }
  .letterhead .wordmark { font-size: 24px; }
  .letterhead .wordmark .dot { width: 10px; height: 10px; }
  .letterhead .tagline { font-size: 9px; margin-top: 6px; color: #9f9296; }
  .return-line { position: absolute; left: 72px; top: 112px; font-size: 5px; }
  .fold-mark { position: absolute; width: 1px; height: 1px; background: #333; }
  .side-mark { position: absolute; left: 0; width: 18px; height: 1px; background: #e6e6e6; }
  .letterhead .footer {
    position: absolute; left: 0; right: 0; bottom: 0; height: 63px;
    background: var(--mauve); color: #fff; font-size: 6.6px; line-height: 1.3;
  }
  .footer .col {
    position: absolute; top: 10px; bottom: 0; padding-left: 8px;
    border-left: 1px solid rgba(255,255,255,0.85);
  }
  .footer .c1 { left: 40px; }
  .footer .c2 { left: 180px; }
  .footer .c3 { left: 310px; }
  .base-rule {
    position: absolute; left: 20px; right: 20px; top: 1175px; height: 8px;
    border: 1px solid #eee; background: #fafafa;
  }
</style>
</head>
<body>
  <section class="brand-panel">
    <div class="wordmark"><span class="dot"></span>Lindenhof</div>
    <div class="tagline">Praxis für Logopädie</div>
  </section>

  <article class="card card-hours">
    <div class="head">
      <div class="wordmark"><span class="dot"></span>Lindenhof</div>
      <div class="tagline">Praxis für Logopädie</div>
    </div>
    <div class="band">
      <span>Sprechzeiten:</span>
      <span>Montag bis Freitag: 08:30–12:00 Uhr</span>
      <span>Montag und Donnerstag: 14:00–17:00 Uhr</span>
    </div>
  </article>

  <article class="card card-contact">
    <div class="head">
      <div class="wordmark"><span class="dot"></span>Lindenhof</div>
    </div>
    <div class="band">
      <span class="name">Lindenhof</span>
      <span class="sub">Praxis für Logopädie</span>
      <span>Birkenweg 14 • 20457 Wiesental</span>
      <span>Telefon: +49 (0)421 558201</span>
      <span>E-Mail: info@lindenhof-praxis.com • www.lindenhof-praxis.com</span>
    </div>
  </article>

  <article class="letterhead">
    <div class="top-band"></div>
    <div class="sender-logo">
      <div class="wordmark"><span class="dot"></span>Lindenhof</div>
      <div class="tagline">Praxis für Logopädie</div>
    </div>
    <span class="fold-mark" style="left:45px;top:103px"></span>
    <span class="fold-mark" style="left:233px;top:103px"></span>
    <span class="fold-mark" style="left:45px;top:200px"></span>
    <span class="fold-mark" style="left:233px;top:200px"></span>
    <div class="return-line">Lindenhof • Birkenweg 14 • 20457 Wiesental</div>
    <span class="side-mark" style="top:236px"></span>
    <span class="side-mark" style="top:333px;width:10px"></span>
    <span class="side-mark" style="top:471px"></span>
    <div class="footer">
      <div class="col c1">Birkenweg 14<br>20457 Wiesental<br>Telefon: +49 (0) 421 558 201<br>info@lindenhof-praxis.de<br>www.lindenhof-praxis.de</div>
      <div class="col c2">Geschäftsführer:<br>Jule Berkhan<br>USt-IdNr. DE318552047<br>Steuernummer: 27/114/05831</div>
      <div class="col c3">Wiesentaler Bank<br>BIC: WTBKDE21XXX<br>IBAN: DE48 2905 0101 0082 4417 36</div>
    </div>
  </article>

  <div class="base-rule"></div>
</body>
</html>
```